Design a single page Shopify store web page

We are looking to have a page designed for a single page Shopify store with 2 products. We already have a basic structure that we like, though we are open to suggestions. We are looking for somebody to provide a design/color scheme that we can then implement using Shopify's templating system. We can handle the implementation(HTML / CSS / jS) as we already have 2 web developers on the team, but have not been able to find a design we liked.

The job would consist of providing a mockup (photoshop or otherwise) and any vector graphics you choose to create for the site (we can provide product photos and other images).

You can also look at http://brickdune.com.au for some of our design direction we have used so far

Target Market(s)

Young Australian Males (18 - 49)

Industry/Entity Type

Store

Number of Pages Required

1 page

Font styles to use
Serif
Sans Serif

Requirements
Must have
• Single Page Design
• E-commerce Product Purchase
• Manly (whatever interpretation of that you have)

```html
<!DOCTYPE html>
<html lang="en">
<head>
<meta charset="utf-8">
<title>Brick Dune — Automate Your Life</title>
<link href="https://fonts.googleapis.com/css2?family=Open+Sans:wght@400;600;700;800&display=swap" rel="stylesheet">
<style>
:root{
  --ink:#2a2a2a;
  --header:#262626;
  --hero-panel:#333333;
  --plans-bg:#666666;
  --about-bg:#ebebeb;
  --footer:#2b2b2b;
  --white:#ffffff;
  --muted:#7a7a7a;
  --footer-text:#c9c9c9;
  --btn-grey:#d5d5d5;
  --green:#13a84a;
  --photo-skin:#8a6a55;
  --photo-wall:#b8b9b7;
}
*{box-sizing:border-box;margin:0;padding:0}
html,body{width:1200px;height:3203px;overflow:hidden}
body{font-family:"Open Sans",Arial,sans-serif;color:var(--ink);background:var(--white)}

.site-header{height:122px;background:var(--header);display:flex;align-items:center;padding:0 70px;color:var(--white)}
.brand{display:flex;align-items:center;gap:18px;font-size:38px;font-weight:600;letter-spacing:1px}
.brand-mark{width:44px;height:44px;border:3px solid var(--white);border-radius:50%}
.main-nav{margin-left:auto;display:flex;gap:42px;font-size:15px;align-items:center}
.main-nav a{color:#dcdcdc;text-decoration:none}
.main-nav a.active{color:var(--white);font-weight:600}
.main-nav a.signup{color:var(--white);text-decoration:underline;margin-left:80px;font-weight:600}

.hero{height:678px;display:flex}
.hero-photo{width:767px;height:100%;background:radial-gradient(ellipse at 45% 45%,var(--photo-skin) 0 22%,#a5a7a5 40%,var(--photo-wall) 70%)}
.hero-panel{flex:1;background:var(--hero-panel);color:var(--white);text-align:right;padding:200px 100px 0 0}
.hero-title{font-size:40px;font-weight:800;line-height:48px;letter-spacing:1px}
.hero-sub{font-size:26px;line-height:37px;margin-top:14px;color:#e8e8e8}
.hero-dots{display:inline-flex;gap:10px;background:#1e1e1e;border-radius:14px;padding:6px 10px;margin-top:22px}
.hero-dots span{width:11px;height:11px;border-radius:50%;background:var(--white)}
.hero-dots span.current{background:transparent;border:2px solid var(--white)}

.section-title{font-size:42px;font-weight:800;text-align:center;letter-spacing:1px}

.how{height:530px;padding-top:75px}
.steps{display:flex;justify-content:center;gap:0;margin-top:45px}
.step{width:360px;text-align:center}
.step-icon{width:210px;height:210px;border-radius:50%;background:#333;margin:0 auto;display:flex;align-items:center;justify-content:center}
.step-name{font-size:28px;margin-top:22px}
.step-text{font-size:13px;color:var(--muted);line-height:19px;margin:8px auto 0;width:280px}

.plans{height:677px;background:var(--plans-bg);padding-top:68px;color:var(--white)}
.plans .section-title{color:var(--white)}
.plan-list{display:flex;justify-content:center;gap:110px;margin-top:40px}
.plan{width:483px;height:325px;background:var(--white);padding:8px;display:flex;gap:6px}
.plan-photo{width:312px;height:100%;background:linear-gradient(180deg,#6b5142 0%,#3b2f2a 55%,#1b1c20 100%)}
.plan-photo.dark{background:linear-gradient(180deg,#262628 0%,#4a3a33 35%,#141416 100%)}
.plan-info{flex:1;display:flex;flex-direction:column;gap:8px;color:var(--ink)}
.plan-name{font-size:28px;line-height:34px}
.plan-option{background:var(--btn-grey);font-size:14px;font-weight:600;text-transform:uppercase;text-align:center;height:50px;line-height:50px;border:1px solid #bbb}
.plan-price{font-size:40px;font-weight:800;margin-top:8px;line-height:56px}
.plan-buy{background:var(--green);color:var(--white);font-size:24px;font-weight:700;text-align:center;height:52px;line-height:52px;margin-top:auto}
.perks{display:grid;grid-template-columns:250px 250px;justify-content:center;row-gap:20px;margin-top:36px;font-size:21px;font-weight:600;margin-left:-40px}
.perk{display:flex;align-items:center;gap:12px}

.faq{height:648px;padding-top:80px}
.faq-grid{display:grid;grid-template-columns:repeat(3,330px);justify-content:center;column-gap:30px;row-gap:36px;margin-top:32px;text-align:center}
.faq-q{font-size:21px;font-weight:600;line-height:25px}
.faq-a{font-size:13px;color:var(--muted);line-height:21px;margin-top:6px}

.about{height:330px;background:var(--about-bg);padding-top:75px}
.about-text{width:1090px;margin:18px auto 0;font-size:12.5px;line-height:25px;text-align:center;color:#555}

.site-footer{height:218px;background:var(--footer);color:var(--footer-text);text-align:center;font-size:13px;padding-top:38px}
.footer-links{display:flex;justify-content:center;gap:10px}
.footer-links span.sep{color:#888}
.footer-line{margin-top:16px}
.footer-badges{display:flex;justify-content:center;gap:9px;margin-top:25px;align-items:center}
.social{width:32px;height:32px;background:#5a7ea8;border-radius:3px}
.pay{width:44px;height:28px;background:#e4e4e4;border-radius:3px}
.pay.first{margin-left:30px}
.pay.blue{background:#2a4c9b}
</style>
</head>
<body>
<header class="site-header">
  <div class="brand"><span class="brand-mark"></span>Brick Dune</div>
  <nav class="main-nav">
    <a class="active" href="#how">How it works</a>
    <a href="#plans">Plans</a>
    <a href="#faq">FAQ</a>
    <a href="#about">About us</a>
    <a class="signup" href="#plans">Sign Up Now!</a>
  </nav>
</header>

<section class="hero">
  <div class="hero-photo" role="img" aria-label="Photo of a muscular man in white briefs leaning against a grey wall"></div>
  <div class="hero-panel">
    <h1 class="hero-title">AUTOMATE<br>YOUR LIFE</h1>
    <p class="hero-sub">New Underwear<br>And Socks<br>Delivered to your door<br>when you need it</p>
    <div class="hero-dots"><span class="current"></span><span></span><span></span><span></span></div>
  </div>
</section>

<section class="how" id="how">
  <h2 class="section-title">HOW IT WORKS</h2>
  <div class="steps">
    <div class="step">
      <div class="step-icon"><svg width="62" height="62" viewBox="0 0 62 62"><rect x="6" y="10" width="42" height="44" rx="6" fill="none" stroke="#fff" stroke-width="6"/><path d="M26 40l4-12L50 8l8 8-20 20z" fill="#fff" stroke="#333" stroke-width="3"/></svg></div>
      <h3 class="step-name">Choose a Plan</h3>
      <p class="step-text">There will be plans for all budgets and styles.</p>
    </div>
    <div class="step">
      <div class="step-icon"><svg width="66" height="66" viewBox="0 0 66 66"><path d="M33 4c3 0 5 3 5 8v14l22 13v7L38 39v12l7 6v5l-12-4-12 4v-5l7-6V39L6 46v-7l22-13V12c0-5 2-8 5-8z" fill="#fff" transform="rotate(45 33 33)"/></svg></div>
      <h3 class="step-name">Choose How Often</h3>
      <p class="step-text">Decide whether you would like to recieve new packages every 3 or 6 months</p>
    </div>
    <div class="step">
      <div class="step-icon"><svg width="62" height="54" viewBox="0 0 62 54"><rect x="3" y="3" width="56" height="48" rx="6" fill="none" stroke="#fff" stroke-width="6"/><rect x="3" y="3" width="56" height="14" fill="#fff"/><circle cx="12" cy="10" r="2.5" fill="#333"/><circle cx="20" cy="10" r="2.5" fill="#333"/><circle cx="28" cy="10" r="2.5" fill="#333"/></svg></div>
      <h3 class="step-name">Get your Pack</h3>
      <p class="step-text">We'll send out your first pack right away and then again every 3 or 6 months</p>
    </div>
  </div>
</section>

<section class="plans" id="plans">
  <h2 class="section-title">PLANS</h2>
  <div class="plan-list">
    <article class="plan">
      <div class="plan-photo" role="img" aria-label="Product photo of a man's torso wearing dark trunks"></div>
      <div class="plan-info">
        <h3 class="plan-name">Comfort</h3>
        <div class="plan-option">Etiam volutpat</div>
        <div class="plan-option">Suspendisse</div>
        <div class="plan-price">$30</div>
        <div class="plan-buy">GET IT!</div>
      </div>
    </article>
    <article class="plan">
      <div class="plan-photo dark" role="img" aria-label="Product photo of a man wearing black boxer briefs, seen from behind"></div>
      <div class="plan-info">
        <h3 class="plan-name">Style</h3>
        <div class="plan-option">Sed nec</div>
        <div class="plan-option">Donec eu</div>
        <div class="plan-price">$30</div>
        <div class="plan-buy">GET IT!</div>
      </div>
    </article>
  </div>
  <div class="perks">
    <div class="perk"><svg width="34" height="24" viewBox="0 0 34 24"><rect x="0" y="3" width="20" height="14" fill="#fff"/><path d="M21 7h7l5 5v5H21z" fill="#fff"/><circle cx="7" cy="19" r="3.5" fill="#fff" stroke="#666" stroke-width="1.5"/><circle cx="26" cy="19" r="3.5" fill="#fff" stroke="#666" stroke-width="1.5"/></svg>Free Shipping</div>
    <div class="perk"><svg width="26" height="28" viewBox="0 0 26 28"><path d="M6 14V5a2 2 0 014 0v7V3a2 2 0 014 0v9V4a2 2 0 014 0v9-6a2 2 0 014 0v11c0 6-4 9-9 9-4 0-6-2-8-5l-5-7a2 2 0 013-2z" fill="#fff"/></svg>Cancel Whenever</div>
    <div class="perk"><svg width="28" height="26" viewBox="0 0 28 26"><path d="M23 13a10 10 0 11-3-7" fill="none" stroke="#fff" stroke-width="3.5"/><path d="M16 2h9v9z" fill="#fff"/></svg>Easy Returns</div>
    <div class="perk"><svg width="28" height="28" viewBox="0 0 28 28"><circle cx="13" cy="15" r="11" fill="none" stroke="#fff" stroke-width="3"/><path d="M7 14l6 6L27 3" fill="none" stroke="#fff" stroke-width="4"/></svg>Satisfaction Guaranteed</div>
  </div>
</section>

<section class="faq" id="faq">
  <h2 class="section-title">FAQ</h2>
  <div class="faq-grid">
    <div><h3 class="faq-q">What is Brick Dune?</h3><p class="faq-a">Donec interdum vulputate accumsan. Sed vitae tortor sit amet arcu tempus imperdiet. Fusce viverra eu est at semper.</p></div>
    <div><h3 class="faq-q">What is your<br>Satisfaction Guarantee?</h3><p class="faq-a">Donec interdum vulputate accumsan. Sed vitae tortor sit amet arcu tempus imperdiet. Fusce viverra eu est at semper.</p></div>
    <div><h3 class="faq-q">Shipping Policy?</h3><p class="faq-a">Donec interdum vulputate accumsan. Sed vitae tortor sit amet arcu tempus imperdiet. Fusce viverra eu est at semper.</p></div>
    <div><h3 class="faq-q">What is Brick Dune?</h3><p class="faq-a">Donec interdum vulputate accumsan. Sed vitae tortor sit amet arcu tempus imperdiet. Fusce viverra eu est at semper.</p></div>
    <div><h3 class="faq-q">What is your<br>Satisfaction Guarantee?</h3><p class="faq-a">Donec interdum vulputate accumsan. Sed vitae tortor sit amet arcu tempus imperdiet. Fusce viverra eu est at semper.</p></div>
    <div><h3 class="faq-q">Shipping Policy?</h3><p class="faq-a">Donec interdum vulputate accumsan. Sed vitae tortor sit amet arcu tempus imperdiet. Fusce viverra eu est at semper.</p></div>
    <div><h3 class="faq-q">What is Brick Dune?</h3><p class="faq-a">Donec interdum vulputate accumsan. Sed vitae tortor sit amet arcu tempus imperdiet. Fusce viverra eu est at semper.</p></div>
    <div><h3 class="faq-q">What is your<br>Satisfaction Guarantee?</h3><p class="faq-a">Donec interdum vulputate accumsan. Sed vitae tortor sit amet arcu tempus imperdiet. Fusce viverra eu est at semper.</p></div>
    <div><h3 class="faq-q">Shipping Policy?</h3><p class="faq-a">Donec interdum vulputate accumsan. Sed vitae tortor sit amet arcu tempus imperdiet. Fusce viverra eu est at semper.</p></div>
  </div>
</section>

<section class="about" id="about">
  <h2 class="section-title">ABOUT US</h2>
  <p class="about-text">Etiam volutpat, turpis in facilisis semper, felis justo vehicula felis, sagittis tempor mauris nisi quis magna. Curabitur erat urna, bibendum ac quam at, vulputate tincidunt ipsum. Cras gravida ornare lacus, non dignissim lorem placerat quis. Ut quam dolor, efficitur a rhoncus vel, varius quis velit. Duis sed convallis sem. Pellentesque habitant morbi tristique senectus et netus et malesuada fames ac turpis egestas. Integer tempus vestibulum orci, eget aliquet leo mollis vel. Praesent id sem imperdiet, commodo nisl a, consequat tellus. Vivamus rutrum et turpis dignissim euismod. Aliquam egestas turpis sit amet tincidunt fermentum. Nunc enim est, eleifend non tincidunt scelerisque, placerat sed eros.</p>
</section>

<footer class="site-footer">
  <div class="footer-links">
    <span>How it works</span><span class="sep">/</span><span>Plans</span><span class="sep">/</span><span>FAQ</span><span class="sep">/</span><span>About us</span><span class="sep">/</span><span>Shipping</span><span class="sep">/</span><span>Returns</span><span class="sep">/</span><span>Payment</span><span class="sep">/</span><span>Terms of Use</span><span class="sep">/</span><span>Privacy Police</span>
  </div>
  <p class="footer-line">Call : 555 010 4827 &nbsp;&nbsp; - &nbsp;&nbsp; E-mail : hello@brickdune.com.au</p>
  <p class="footer-line">Copyright © 2014 &nbsp;Brick Dune. &nbsp;&nbsp;All rights reserved</p>
  <div class="footer-badges">
    <span class="social"></span><span class="social"></span><span class="social"></span><span class="social"></span>
    <span class="pay first"></span><span class="pay"></span><span class="pay blue"></span><span class="pay"></span>
  </div>
</footer>
</body>
</html>
```